Coastline Premier Retreats Business Card Design

Design a business card for Coastline Premier Retreats. Look at the website for colors and reference. Card should have logo, name, title, office number, mobile number, email, URL and a tagline like, "Luxury Hotel & Resort Email Marketing" (This might change).

https://www.coastlinepremierretreats.example

The rest I will leave up to your imagination.

Contact Information for Business Card

Logo, name, title, office number, mobile number, email, URL and a tagline like, "Luxury Hotel & Resort Email Marketing" (This might change).

```html
<!DOCTYPE html>
<html lang="en">
<head>
<meta charset="utf-8">
<title>Coastline Premier Retreats – Business Card</title>
<link href="https://fonts.googleapis.com/css2?family=Montserrat:wght@400;500;700&display=swap" rel="stylesheet">
<style>
  :root {
    --page-bg: #2b2b2c;
    --card-bg: #1d1d1e;
    --accent: #e8761c;
    --text-light: #f2f2f2;
    --logo-grey: #6f6f72;
  }
  * { box-sizing: border-box; margin: 0; padding: 0; }
  html, body { width: 1200px; height: 915px; overflow: hidden; }
  body {
    background: var(--page-bg);
    font-family: "Montserrat", Arial, sans-serif;
    display: flex;
    align-items: center;
    justify-content: center;
    gap: 40px;
  }
  .card {
    position: relative;
    width: 560px;
    height: 320px;
    background: var(--card-bg);
    border-radius: 18px;
    overflow: hidden;
  }

  /* Front side */
  .card-front {
    display: flex;
    flex-direction: column;
    align-items: center;
    justify-content: center;
  }
  .front-brand {
    color: var(--logo-grey);
    font-weight: 700;
    font-size: 30px;
    letter-spacing: 2px;
    text-transform: uppercase;
    text-align: center;
    line-height: 1.15;
  }
  .tagline {
    margin-top: 34px;
    color: var(--accent);
    font-weight: 500;
    font-size: 15px;
  }

  /* Back side */
  .brand-column {
    position: absolute;
    left: 0; top: 0;
    width: 160px; height: 100%;
    display: flex;
    align-items: center;
    justify-content: center;
  }
  .brand-vertical {
    transform: rotate(-90deg);
    white-space: nowrap;
    color: var(--text-light);
    font-weight: 700;
    font-size: 16px;
    letter-spacing: 1.5px;
    text-transform: uppercase;
    line-height: 1.25;
    display: flex;
    align-items: center;
    gap: 12px;
  }
  .brand-mark {
    width: 12px; height: 12px;
    flex: none;
    background: var(--accent);
  }
  .divider {
    position: absolute;
    left: 160px; top: 48px;
    width: 1px; height: 224px;
    background: var(--accent);
  }
  .details {
    position: absolute;
    left: 194px; top: 52px;
    color: var(--text-light);
  }
  .person-name {
    color: var(--accent);
    font-weight: 700;
    font-size: 26px;
    letter-spacing: 0.5px;
    text-transform: uppercase;
    line-height: 1;
  }
  .person-title {
    margin-top: 6px;
    font-size: 14px;
  }
  .address {
    margin-top: 22px;
    font-size: 13.5px;
    line-height: 1.35;
    font-style: normal;
  }
  .contact-list {
    list-style: none;
    margin-top: 18px;
    font-size: 13.5px;
  }
  .contact-list li {
    display: flex;
    align-items: center;
    gap: 10px;
    line-height: 1.55;
  }
  .contact-icon {
    width: 11px; height: 11px;
    flex: none;
    fill: var(--accent);
  }
</style>
</head>
<body>

  <section class="card card-front" aria-label="Card front">
    <div class="front-brand">Coastline Premier<br>Retreats</div>
    <p class="tagline">Luxury Hotel &amp; Resort Email Marketing</p>
  </section>

  <section class="card card-back" aria-label="Card back">
    <div class="brand-column">
      <div class="brand-vertical"><span class="brand-mark"></span><span>Coastline Premier<br>Retreats</span></div>
    </div>
    <div class="divider"></div>

    <div class="details">
      <h1 class="person-name">Marcus Hale</h1>
      <p class="person-title">CEO/Founder</p>
      <address class="address">Po Box, 480 B Harbor Rd<br>North America, AB 47012</address>
      <ul class="contact-list">
        <li>
          <svg class="contact-icon" viewBox="0 0 12 12" aria-hidden="true"><rect x="3" y="0.5" width="6" height="11" rx="1"/><rect x="4" y="1.8" width="4" height="7" fill="#1d1d1e"/></svg>
          555.014.2200
        </li>
        <li>
          <svg class="contact-icon" viewBox="0 0 12 12" aria-hidden="true"><path d="M1 4c0-2 2-3 5-3s5 1 5 3v1H8.5V3.8h-5V5H1z"/><rect x="2" y="6" width="8" height="5" rx="1"/></svg>
          +34 600 000 217
        </li>
        <li>
          <svg class="contact-icon" viewBox="0 0 12 12" aria-hidden="true"><path d="M0.5 2.5h11v7h-11z"/><path d="M0.5 2.5L6 6.5l5.5-4" stroke="#1d1d1e" stroke-width="1" fill="none"/></svg>
          info@coastlinepremierretreats.example
        </li>
        <li>
          <svg class="contact-icon" viewBox="0 0 12 12" aria-hidden="true"><circle cx="6" cy="6" r="5.5"/><path d="M0.5 6h11M6 0.5c-2.5 3-2.5 8 0 11M6 0.5c2.5 3 2.5 8 0 11" stroke="#1d1d1e" stroke-width="0.9" fill="none"/></svg>
          www.coastlinepremierretreats.example
        </li>
      </ul>
    </div>
  </section>

</body>
</html>
```